Business Card Design

I already have a company logo for my company. I have a logo for the manufacturer we represent. I want a professional business card design.

```html
<!DOCTYPE html>
<html lang="en">
<head>
<meta charset="utf-8">
<title>Signalguard LLC — Business Card</title>
<link href="https://fonts.googleapis.com/css2?family=Open+Sans:wght@400;600;700&display=swap" rel="stylesheet">
<style>
  :root {
    --bg-top: #5a5a5a;
    --bg-bottom: #1c1c1c;
    --card: #161616;
    --red: #e3202a;
    --white: #f2f2f2;
    --grey: #d8d8d8;
  }
  * { box-sizing: border-box; margin: 0; padding: 0; }
  html, body { width: 1200px; height: 780px; overflow: hidden; }
  body {
    position: relative;
    background: linear-gradient(160deg, var(--bg-top), var(--bg-bottom));
    font-family: "Open Sans", sans-serif;
  }
  .card {
    position: absolute;
    background: var(--card);
    border-radius: 22px;
    overflow: hidden;
    box-shadow: 0 18px 40px rgba(0,0,0,.45);
  }
  /* Front: portrait contact side */
  .card-front { left: 110px; top: 100px; width: 340px; height: 580px; }
  .card-front .trim { position: absolute; inset: 0; }
  .front-brand {
    position: absolute; left: 34px; top: 92px;
    display: flex; align-items: center; gap: 10px;
    color: var(--white); font-weight: 700; font-size: 25px; letter-spacing: .5px;
  }
  .brand-dot { width: 16px; height: 16px; border-radius: 50%; background: var(--red); flex: none; }
  .contact {
    position: absolute; right: 34px; bottom: 70px;
    text-align: right; color: var(--grey);
  }
  .contact .small-brand {
    display: inline-flex; align-items: center; gap: 7px;
    color: var(--white); font-weight: 700; font-size: 16px; margin-bottom: 26px;
  }
  .contact .small-brand .brand-dot { width: 10px; height: 10px; }
  .contact .address { font-size: 13px; margin-bottom: 18px; }
  .contact ul { list-style: none; font-size: 13px; line-height: 1.75; margin-bottom: 22px; }
  .contact li { display: flex; justify-content: flex-end; align-items: center; gap: 7px; }
  .contact li svg { width: 12px; height: 12px; fill: var(--red); }
  .person-name { color: var(--red); font-weight: 700; font-size: 22px; letter-spacing: .5px; line-height: 1.1; }
  .person-role { color: var(--grey); font-size: 13px; margin-top: 4px; }
  .edge-band { position: absolute; right: 0; bottom: 0; width: 26px; height: 96px; background: var(--red); }

  /* Back: landscape brand side */
  .card-back { left: 500px; top: 220px; width: 600px; height: 340px; }
  .back-brand {
    position: absolute; inset: 0;
    display: flex; align-items: center; justify-content: center; gap: 16px;
    color: var(--white); font-weight: 700; font-size: 40px; letter-spacing: 1px;
  }
  .back-brand .brand-dot { width: 26px; height: 26px; }
</style>
</head>
<body>
  <section class="card card-front" aria-label="Business card, contact side">
    <svg class="trim" viewBox="0 0 340 580" aria-hidden="true">
      <polygon points="262,0 282,0 92,235 72,235" fill="var(--red)"/>
      <polygon points="294,0 314,0 124,235 104,235" fill="var(--red)"/>
      <polygon points="326,0 340,0 340,4 156,235 136,235" fill="var(--red)"/>
      <polygon points="0,290 150,290 130,310 0,310" fill="var(--red)"/>
      <polygon points="0,322 175,322 155,342 0,342" fill="var(--red)"/>
    </svg>
    <div class="front-brand"><span class="brand-dot"></span>SIGNALGUARD</div>

    <div class="contact">
      <div class="small-brand"><span class="brand-dot"></span>SIGNALGUARD LLC</div>
      <p class="address">48 Harbor Lane, Fairview, OH 44120</p>
      <ul>
        <li>555 204 318
          <svg viewBox="0 0 24 24"><path d="M6.6 10.8a15 15 0 0 0 6.6 6.6l2.2-2.2a1 1 0 0 1 1-.25 11.4 11.4 0 0 0 3.6.57 1 1 0 0 1 1 1V20a1 1 0 0 1-1 1A17 17 0 0 1 3 4a1 1 0 0 1 1-1h3.5a1 1 0 0 1 1 1c0 1.25.2 2.45.57 3.57a1 1 0 0 1-.25 1z"/></svg></li>
        <li>info@signalguard.co
          <svg viewBox="0 0 24 24"><path d="M2 5h20v14H2zm2 2v.5l8 5 8-5V7l-8 5z"/></svg></li>
        <li>www.signalguard.co
          <svg viewBox="0 0 24 24"><circle cx="12" cy="12" r="10"/></svg></li>
      </ul>
      <p class="person-name">DANIEL REYES</p>
      <p class="person-role">Managing Director</p>
    </div>
    <div class="edge-band"></div>
  </section>

  <section class="card card-back" aria-label="Business card, brand side">
    <div class="back-brand"><span class="brand-dot"></span>SIGNALGUARD LLC</div>
  </section>
</body>
</html>
```